OBK Farcoast Logistics Limited

We need the buissnes card to be very exclusive. As we are all young in our company. We need this to be the gate to make our clients feel deep interest for us.

We are focused in as International Trade advisors, and our products go from Oil Tanker Ships to Rubber balls for dogs.

Our Slogan is Bringing World Home.
And our main marketing will be through Internet.

We were stablished in 2009 In Mexico and we also have offices in Hong Kong.
We have representatives in China and Europe.

Target Market(s)

Is every company or Individual that wants to develop an International Project or product development or Logistic service of Goods and people.
Some of our current projects are Ship Brokerage, Mine Brokerage, Real State and Product Pormotional development.

Industry/Entity Type

It Company

Requirements
Must have
• Our Logo and slogan, and make the card accoriding to the logo.
Nice to have
• Our Colors

```html
<!DOCTYPE html>
<html lang="en">
<head>
<meta charset="utf-8">
<title>OBK Business Card</title>
<link rel="stylesheet" href="https://fonts.googleapis.com/css2?family=Source+Sans+3:wght@400;600;700&display=swap">
<style>
  :root {
    --stage: #e9eaee;
    --card-dark: #333333;
    --brand-blue: #00aeef;
    --brand-green: #8dc63f;
    --ink-light: #ffffff;
  }
  * { margin: 0; padding: 0; box-sizing: border-box; }
  html, body {
    width: 1200px; height: 987px; overflow: hidden;
    background: var(--stage);
    font-family: "Source Sans 3", Arial, sans-serif;
  }
  .card {
    position: absolute; left: 220px;
    width: 760px; height: 434px;
    background: var(--card-dark);
    border-radius: 34px;
    overflow: hidden;
    box-shadow: 0 6px 18px rgba(0,0,0,.18);
  }
  .card--back { top: 36px; }
  .card--front { top: 517px; }

  /* back side */
  .back-brand {
    position: absolute; left: 0; right: 0; top: 88px;
    display: flex; align-items: center; justify-content: center; gap: 18px;
  }
  .brand-dot {
    width: 64px; height: 64px; border-radius: 50%;
    background: var(--brand-blue);
  }
  .brand-name {
    font-weight: 700; font-size: 96px; line-height: 1;
    color: var(--brand-green); letter-spacing: 4px;
  }
  .back-slogan {
    position: absolute; left: 0; right: 0; top: 236px;
    text-align: center; color: var(--brand-green);
    font-size: 30px; letter-spacing: 2px;
  }
  .back-web {
    position: absolute; left: 0; right: 0; top: 288px;
    text-align: center; color: var(--ink-light);
    font-size: 28px; letter-spacing: 6px;
  }

  /* front side */
  .front-band { position: absolute; inset: 0; }
  .front-brand {
    position: absolute; left: 0; right: 0; top: 56px; text-align: center;
  }
  .front-brand .brand-name { font-size: 80px; letter-spacing: 3px; }
  .front-slogan {
    color: var(--brand-blue); font-size: 18px; margin-top: 4px;
  }
  .person {
    position: absolute; right: 452px; top: 272px;
    text-align: right; color: var(--ink-light);
  }
  .person-name { font-weight: 700; font-size: 28px; line-height: 1.1; }
  .person-title { font-size: 21px; line-height: 1.3; }
  .person-address { font-size: 20px; line-height: 1.25; margin-top: 2px; }
  .divider {
    position: absolute; left: 324px; top: 276px;
    width: 2px; height: 126px; background: var(--ink-light);
  }
  .contacts {
    position: absolute; left: 342px; top: 282px;
    list-style: none; color: var(--ink-light);
    font-size: 21px; line-height: 30px;
  }
  .contacts li { display: flex; align-items: center; gap: 8px; white-space: nowrap; }
  .contacts svg { width: 18px; height: 18px; flex: none; }
</style>
</head>
<body>

<section class="card card--back" aria-label="Card back">
  <div class="back-brand">
    <span class="brand-dot"></span>
    <span class="brand-name">OBK</span>
  </div>
  <p class="back-slogan">BRINGING WORLD HOME</p>
  <p class="back-web">www.obkfc-trade.net</p>
</section>

<section class="card card--front" aria-label="Card front">
  <svg class="front-band" viewBox="0 0 760 434" width="760" height="434" aria-hidden="true">
    <path d="M0,160 Q530,188 736,434" fill="none" stroke="var(--brand-green)" stroke-width="3"/>
    <path d="M0,170 Q520,200 720,434 L0,434 Z" fill="var(--brand-blue)"/>
  </svg>

  <div class="front-brand">
    <div class="brand-name">OBK</div>
    <div class="front-slogan">Bringing World Home</div>
  </div>

  <div class="person">
    <p class="person-name">Your Name</p>
    <p class="person-title">Title</p>
    <p class="person-address">Street Name, City Name<br>State Zip Code</p>
  </div>

  <span class="divider"></span>

  <ul class="contacts">
    <li>
      <svg viewBox="0 0 20 20"><circle cx="10" cy="10" r="9" fill="none" stroke="#fff" stroke-width="1.6"/><path d="M7 5c-1 1-1 3 1 6s4 4 5 3l1-1-2-2-1 1c-1-.5-2-1.5-2.5-2.5l1-1-2-2z" fill="#fff"/></svg>
      123-456-0789
    </li>
    <li>
      <svg viewBox="0 0 20 20"><rect x="5" y="1.5" width="10" height="17" rx="2" fill="none" stroke="#fff" stroke-width="1.6"/><rect x="7" y="4" width="6" height="7" fill="#fff"/><circle cx="10" cy="15" r="1.2" fill="#fff"/></svg>
      123-456-0789
    </li>
    <li>
      <svg viewBox="0 0 20 20"><rect x="1.5" y="4" width="17" height="12" rx="1.5" fill="#fff"/><path d="M2 5l8 6 8-6" fill="none" stroke="var(--brand-blue)" stroke-width="1.6"/></svg>
      info@obkfc-trade.net
    </li>
    <li>
      <svg viewBox="0 0 20 20"><circle cx="10" cy="10" r="8.5" fill="none" stroke="#fff" stroke-width="1.6"/><ellipse cx="10" cy="10" rx="3.6" ry="8.5" fill="none" stroke="#fff" stroke-width="1.4"/><path d="M2 10h16M3.5 6h13M3.5 14h13" stroke="#fff" stroke-width="1.2"/></svg>
      www.obkfc-trade.net
    </li>
  </ul>
</section>

</body>
</html>
```